New Business card design to reflect rebrand

I would like a business card design with a good base colour for our new logo and also a placeholder for a profile pic of the card holder. the design needs to be editable to the point that we can easily change the picture of the person and use that design for printmerlo etc. we are looking at a metalic finish business card so will need a good base colour to bring out the finish.

Target Market(s)

prospective customers

Industry/Entity Type

Business

Contact Information for Business Card

I would like one editable design that we can change the name of the card holder and profile picture. The design need to be in a format that be send to printmerlo etc.

Our address is Fenwick Lodge, Copse Lane, Ashby Marston, GU14 3TP Tel no. 01483 556172

Requirements
Must have
• place holder for a profile pic for the card holder. in AI or preferably PSD format

```html
<!DOCTYPE html>
<html lang="en">
<head>
<meta charset="utf-8">
<title>Brightmoor Workplace Services – Business Card</title>
<link rel="stylesheet" href="https://fonts.googleapis.com/css2?family=Source+Sans+3:wght@400;600&display=swap">
<style>
  :root {
    --backdrop: #000000;
    --card-orange: #ee6100;
    --card-slate: #435872;
    --photo-tone: #3d4d63;
    --photo-tone-dark: #1c2330;
    --text-light: #ffffff;
    --brand-slate: #435872;
  }
  * { box-sizing: border-box; margin: 0; padding: 0; }
  html, body {
    width: 1200px; height: 900px; overflow: hidden;
    background: var(--backdrop);
    font-family: "Source Sans 3", "Myriad Pro", Arial, sans-serif;
  }
  .canvas { position: relative; width: 1200px; height: 900px; }

  .card { position: absolute; top: 275px; width: 477px; height: 293px; }
  .card-front {
    left: 116px; background: var(--card-orange);
    border-radius: 0 55px 0 55px;
  }
  .card-back {
    left: 622px; background: var(--card-slate);
    border-radius: 55px 0 55px 0;
    display: flex; align-items: center; justify-content: center;
  }

  .profile-photo {
    position: absolute; left: 39px; top: 30px;
    width: 145px; height: 198px; border-radius: 50%;
    background: radial-gradient(ellipse at 50% 35%, var(--photo-tone) 0%, var(--photo-tone) 55%, var(--photo-tone-dark) 100%);
  }
  .holder-name {
    position: absolute; left: 20px; width: 185px; top: 236px;
    text-align: center; color: var(--text-light);
    font-size: 27px; font-weight: 600; letter-spacing: 0.2px;
    white-space: nowrap;
  }

  .brand-front {
    position: absolute; left: 226px; top: 48px;
    color: var(--brand-slate); font-weight: 600;
    display: flex; align-items: center; gap: 8px;
    white-space: nowrap;
  }
  .brand-front .brand-name { font-size: 23px; line-height: 1.1; }
  .brand-dot { width: 12px; height: 12px; border-radius: 50%; background: var(--brand-slate); flex: none; }

  .contact {
    position: absolute; left: 226px; top: 169px;
    color: var(--text-light); font-size: 13px; line-height: 20px;
    white-space: nowrap;
  }
  .contact-row { display: flex; align-items: center; gap: 6px; }
  .contact-row svg { width: 10px; height: 10px; fill: var(--text-light); }
  .address { margin-top: 8px; line-height: 19px; font-size: 13.5px; }

  .brand-back {
    color: var(--text-light); font-weight: 600; text-align: center;
    display: flex; align-items: center; gap: 14px;
    white-space: nowrap;
  }
  .brand-back .brand-name { font-size: 36px; line-height: 1.1; }
  .brand-back .brand-dot { width: 18px; height: 18px; background: var(--card-orange); }
</style>
</head>
<body>
<main class="canvas">
  <section class="card card-front">
    <div class="profile-photo" role="img" aria-label="Profile photo of the card holder"></div>
    <p class="holder-name">Daniel Reeve</p>

    <div class="brand-front">
      <span class="brand-dot"></span>
      <span class="brand-name">Brightmoor<br>Workplace Services</span>
    </div>

    <div class="contact">
      <div class="contact-row">
        <svg viewBox="0 0 10 10" aria-hidden="true"><path d="M2 0.5 L3.6 2.6 L2.8 3.6 Q4 6 6.4 7.2 L7.4 6.4 L9.5 8 L8.4 9.5 Q4.5 9.3 1.9 6.3 Q0.4 4.2 0.5 1.7 Z"/></svg>
        <span>01483 556172</span>
      </div>
      <div class="contact-row">
        <svg viewBox="0 0 10 10" aria-hidden="true"><path d="M0.5 2 H9.5 V8.5 H0.5 Z M0.5 2 L5 5.5 L9.5 2" fill="none" stroke="#fff" stroke-width="1"/><path d="M0.5 2 H9.5 L5 5.5 Z"/></svg>
        <span>info@brightmoor.co.uk</span>
      </div>
      <p class="address">Fenwick Lodge, Copse Lane,<br>Ashby Marston, GU14 3TP</p>
    </div>
  </section>

  <section class="card card-back">
    <div class="brand-back">
      <span class="brand-dot"></span>
      <span class="brand-name">Brightmoor<br>Workplace Services</span>
    </div>
  </section>
</main>
</body>
</html>
```